KTR Business Card Design

We need a business card design for a new company called ' Copper Lantern Roasters'. We are a mobile Coffee Trailer providing Espresso Coffee, Specialty Tea's, Milkshakes, Iced Coffee & Iced Chocolate, Soft drinks and Gourmet Cookies to Sporting Events, Fetes, Animal Shows etc...
We would like Darren's name and mobile phone number on the card along with the copper lantern email address and a link to our facebook page Copper Lantern Roasters.
Can you please attach the Copper Lantern Logo to the business card.
I have tried to attach our logo and a picture of our mobile trailer to give you an idea of how we would like the design similar to the trailer if possible. If these pictures and logo's are not attached please email me and i will send them through.

Industry/Entity Type

Business

Contact Information for Business Card

Darren Wexley
0491 672 308
copperlanternroasters@mailquay.com
FB Copper Lantern Roasters

Requirements
Must have
• We would like coffee beans in the back ground of the card.

```html
<!DOCTYPE html>
<html lang="en">
<head>
<meta charset="utf-8">
<title>KTR Business Card Design</title>
<link href="https://fonts.googleapis.com/css2?family=Exo+2:ital,wght@0,400;0,500;0,600;1,500;1,600&display=swap" rel="stylesheet">
<style>
  :root {
    --page: #e9e9e9;
    --card-light: #ffffff;
    --card-grey: #c9c9c9;
    --cream: #e6e09c;
    --bean-dark: #6b4a2e;
    --bean-light: #a07a52;
    --ink: #1d1d1d;
    --brand: #5e1b1e;
  }
  * { margin: 0; padding: 0; box-sizing: border-box; }
  html, body { width: 1200px; height: 903px; overflow: hidden; }
  body {
    background: var(--page);
    font-family: "Exo 2", "Trebuchet MS", sans-serif;
    color: var(--ink);
    position: relative;
  }
  .card {
    position: absolute;
    left: 290px;
    width: 620px;
    height: 354px;
    box-shadow: 0 10px 26px rgba(0,0,0,.25);
    overflow: hidden;
  }
  .card--back { top: 52px; }
  .card--front { top: 478px; }
  .card__shapes, .card__beans { position: absolute; inset: 0; width: 100%; height: 100%; }

  .brand {
    position: absolute;
    display: flex;
    align-items: center;
    gap: 10px;
    color: var(--brand);
    font-weight: 600;
    font-size: 19px;
    letter-spacing: .3px;
  }
  .brand__dot {
    width: 14px; height: 14px; border-radius: 50%;
    background: var(--brand);
    flex: none;
  }
  .card--back .brand { left: 0; right: 0; top: 78px; justify-content: center; }
  .card--front .brand { left: 34px; top: 150px; font-size: 18px; }

  .back__web {
    position: absolute; left: 290px; top: 226px;
    font-size: 16px; letter-spacing: 2px;
  }
  .back__follow {
    position: absolute; left: 290px; top: 270px;
    display: flex; align-items: center; gap: 10px;
    font-size: 16px; letter-spacing: 1.5px;
  }
  .social { width: 20px; height: 20px; background: var(--ink); border-radius: 3px; }

  .person { position: absolute; left: 322px; top: 30px; }
  .person__name {
    font-size: 22px; font-weight: 600; font-style: italic;
    letter-spacing: 1.5px; text-transform: uppercase;
  }
  .person__role { font-size: 15px; font-style: italic; margin: 2px 0 0 20px; letter-spacing: .6px; }

  .contact {
    position: absolute; right: 26px; top: 164px;
    text-align: right; font-size: 13.5px; letter-spacing: 1px;
  }
  .contact__address { font-size: 15px; line-height: 1.3; margin-bottom: 12px; }
  .contact__row {
    display: flex; justify-content: flex-end; align-items: center;
    gap: 8px; height: 21px;
  }
  .contact__row--small { font-size: 12px; letter-spacing: .6px; }
  .icon { width: 15px; height: 15px; flex: none; }
</style>
</head>
<body>

  <section class="card card--back" aria-label="Card back">
    <svg class="card__shapes" viewBox="0 0 620 354" preserveAspectRatio="none">
      <defs>
        <linearGradient id="backGrey" x1="0" y1="0" x2="1" y2="0.4">
          <stop offset="0" stop-color="var(--card-grey)"/>
          <stop offset="0.45" stop-color="var(--card-light)"/>
          <stop offset="1" stop-color="var(--card-grey)"/>
        </linearGradient>
      </defs>
      <rect width="620" height="354" fill="url(#backGrey)"/>
      <polygon points="0,354 0,330 620,95 620,354" fill="var(--cream)"/>
    </svg>
    <svg class="card__beans" viewBox="0 0 620 354" preserveAspectRatio="none" role="img" aria-label="Coffee beans background">
      <defs>
        <radialGradient id="beansBack" cx="0.15" cy="0.85" r="0.9">
          <stop offset="0" stop-color="var(--bean-dark)" stop-opacity=".22"/>
          <stop offset="0.6" stop-color="var(--bean-light)" stop-opacity=".08"/>
          <stop offset="1" stop-color="var(--bean-light)" stop-opacity="0"/>
        </radialGradient>
      </defs>
      <rect width="620" height="354" fill="url(#beansBack)"/>
    </svg>
    <div class="brand"><span class="brand__dot"></span>Copper Lantern Roasters</div>
    <p class="back__web">www.copperlanternroasters.net</p>
    <div class="back__follow">
      <span>follow us on here:</span>
      <span class="social"></span><span class="social"></span><span class="social"></span><span class="social"></span>
    </div>
  </section>

  <section class="card card--front" aria-label="Card front">
    <svg class="card__shapes" viewBox="0 0 620 354" preserveAspectRatio="none">
      <defs>
        <linearGradient id="frontGrey" x1="0" y1="0" x2="1" y2="0.3">
          <stop offset="0" stop-color="var(--card-grey)"/>
          <stop offset="0.4" stop-color="var(--card-light)"/>
          <stop offset="1" stop-color="var(--card-grey)"/>
        </linearGradient>
      </defs>
      <rect width="620" height="354" fill="url(#frontGrey)"/>
      <polygon points="292,0 620,0 620,30 304,178" fill="var(--cream)"/>
      <polygon points="0,330 540,86 620,230 620,354 0,354" fill="var(--cream)"/>
    </svg>
    <svg class="card__beans" viewBox="0 0 620 354" preserveAspectRatio="none" role="img" aria-label="Coffee beans background">
      <defs>
        <radialGradient id="beansFront" cx="0.1" cy="0.9" r="0.8">
          <stop offset="0" stop-color="var(--bean-dark)" stop-opacity=".22"/>
          <stop offset="0.6" stop-color="var(--bean-light)" stop-opacity=".08"/>
          <stop offset="1" stop-color="var(--bean-light)" stop-opacity="0"/>
        </radialGradient>
      </defs>
      <rect width="620" height="354" fill="url(#beansFront)"/>
    </svg>

    <div class="brand"><span class="brand__dot"></span>Copper Lantern Roasters</div>

    <div class="person">
      <p class="person__name">Darren Wexley</p>
      <p class="person__role">Managing Director</p>
    </div>

    <div class="contact">
      <p class="contact__address">27 Level 4, Quayside<br>Harbour Lane QSD</p>
      <p class="contact__row">07 3184 5526
        <svg class="icon" viewBox="0 0 16 16"><path d="M3 1l3 3-1.6 2a9 9 0 005.6 5.6L12 10l3 3-2 2C6.5 14.5 1.5 9.5 1 3z" fill="var(--ink)"/></svg></p>
      <p class="contact__row">0491 672 308
        <svg class="icon" viewBox="0 0 16 16"><rect x="4" y="1" width="8" height="14" rx="1.5" fill="none" stroke="var(--ink)" stroke-width="1.6"/><circle cx="8" cy="12.5" r=".9" fill="var(--ink)"/></svg></p>
      <p class="contact__row">07 3184 5527
        <svg class="icon" viewBox="0 0 16 16"><rect x="2" y="6" width="12" height="9" fill="var(--ink)"/><rect x="4" y="1" width="7" height="6" fill="none" stroke="var(--ink)" stroke-width="1.4"/></svg></p>
      <p class="contact__row contact__row--small">copperlanternroasters@mailquay.com
        <svg class="icon" viewBox="0 0 16 16"><rect x="1" y="3" width="14" height="10" fill="var(--ink)"/><path d="M1 3l7 6 7-6" fill="none" stroke="var(--cream)" stroke-width="1.2"/></svg></p>
      <p class="contact__row contact__row--small">www.copperlanternroasters.net
        <svg class="icon" viewBox="0 0 16 16"><circle cx="8" cy="8" r="6.5" fill="none" stroke="var(--ink)" stroke-width="1.4"/><ellipse cx="8" cy="8" rx="3" ry="6.5" fill="none" stroke="var(--ink)" stroke-width="1.1"/><path d="M1.5 8h13M2.5 4.8h11M2.5 11.2h11" stroke="var(--ink)" stroke-width="1"/></svg></p>
      <p class="contact__row contact__row--small">FB Copper Lantern Roasters
        <svg class="icon" viewBox="0 0 16 16"><rect x="2" y="2" width="12" height="12" rx="2" fill="var(--ink)"/></svg></p>
    </div>
  </section>

</body>
</html>
```